Brightfen Business Card Redesign & Logo Update

We need to update our business cards to something more modern and fresh. Brightfen can provide the current color schemes and old design examples, but welcome creativity in helping us with this redesign. PLEASE NOTE that we no longer utilize the "tree" and/or "leaf" imagery in our branding. If able would apprecaite an update on the quality of our "words only" logo in Ai. / PNG formats too.

Target Market(s)

Investors, landowners, corporate partners, contractors

Industry/Entity Type

Environmental Restoration & Conservation

Contact Information for Business Card

Logo, persons name, title, mailing address, phone and email, website url

Font styles to use
Other font styles liked:
• Merriweather

Requirements
Nice to have
• Logo, persons name, title, mailing address, phone and email, website url, but open to ideams
Should not have
• No all back backgrounds

```html
<!DOCTYPE html>
<html lang="en">
<head>
<meta charset="utf-8">
<title>Brightfen Business Card</title>
<link href="https://fonts.googleapis.com/css2?family=Montserrat:wght@400;500;700;800&display=swap" rel="stylesheet">
<style>
  :root {
    --brand-green: #177a40;
    --brand-orange: #ee7a1e;
    --ink: #2a2a2a;
    --paper: #ffffff;
    --backdrop: #e9ebe9;
    --card-w: 600px;
    --card-h: 343px;
  }
  * { box-sizing: border-box; margin: 0; padding: 0; }
  html, body {
    width: 1200px; height: 900px; overflow: hidden;
    background: var(--backdrop);
    font-family: "Montserrat", Arial, sans-serif;
  }
  .sheet {
    width: 1200px; height: 900px;
    display: flex; flex-direction: column;
    align-items: center; justify-content: center; gap: 60px;
  }
  .card {
    width: var(--card-w); height: var(--card-h);
    border-radius: 22px;
    box-shadow: 0 10px 28px rgba(0,0,0,0.18);
    position: relative; overflow: hidden;
  }
  /* Front side */
  .card--front {
    background: var(--paper);
    display: flex; align-items: center;
    padding: 0 40px;
  }
  .front__brand {
    flex: 0 0 236px;
    font-weight: 800; font-size: 38px; letter-spacing: 0.5px;
    color: var(--brand-green);
    text-transform: uppercase; white-space: nowrap;
  }
  .front__divider {
    width: 1px; height: 180px; flex: 0 0 1px;
    background: var(--brand-green);
    margin: 0 28px 0 8px;
  }
  .contact { color: var(--ink); white-space: nowrap; }
  .contact__name {
    font-weight: 800; font-size: 19px; letter-spacing: 1.5px;
    text-transform: uppercase; line-height: 1.1;
  }
  .contact__first { color: var(--brand-green); }
  .contact__last { color: var(--brand-orange); }
  .contact__title { font-size: 14px; margin: 4px 0 12px; }
  .contact__address { font-size: 13px; line-height: 1.45; margin-bottom: 10px; }
  .contact__line {
    display: flex; align-items: center; gap: 8px;
    font-size: 13px; line-height: 1.6;
  }
  .contact__icon { width: 12px; height: 12px; flex: 0 0 12px; }
  .contact__icon path, .contact__icon circle { fill: var(--brand-orange); }
  /* Back side */
  .card--back {
    background: var(--brand-green);
    display: flex; align-items: center; justify-content: center;
  }
  .back__brand {
    font-weight: 800; font-size: 72px; letter-spacing: 1px;
    color: var(--paper); text-transform: uppercase;
  }
</style>
</head>
<body>
<main class="sheet">
  <section class="card card--front" aria-label="Business card front">
    <div class="front__brand">Brightfen</div>
    <div class="front__divider"></div>
    <div class="contact">
      <p class="contact__name"><span class="contact__first">Daniel</span> <span class="contact__last">Harper</span></p>
      <p class="contact__title">CEO/Founder</p>
      <p class="contact__address">48 Millbrook Lane<br>Ashford Vale, KT 30918</p>
      <p class="contact__line">
        <svg class="contact__icon" viewBox="0 0 12 12" aria-hidden="true"><path d="M2.5 0.8 4.4 0.5 5.3 3.3 4 4.2c.6 1.5 1.8 2.7 3.3 3.3l.9-1.3 2.8.9-.3 1.9c-.2.8-.9 1.2-1.7 1.1C4.6 9.7 1.8 6.9 1.3 2.5 1.2 1.7 1.7 1 2.5.8Z"/></svg>
        (555) 214 6630
      </p>
      <p class="contact__line">
        <svg class="contact__icon" viewBox="0 0 12 12" aria-hidden="true"><path d="M0.5 2.5 6 7l5.5-4.5v7h-11Z"/></svg>
        daniel@brightfen.com
      </p>
      <p class="contact__line">
        <svg class="contact__icon" viewBox="0 0 12 12" aria-hidden="true"><circle cx="6" cy="6" r="5.5"/></svg>
        www.brightfen.com
      </p>
    </div>
  </section>

  <section class="card card--back" aria-label="Business card back">
    <div class="back__brand">Brightfen</div>
  </section>
</main>
</body>
</html>
```